Re-style home page - eye-catching and unique design for social commerce website

We need a new concept design for BrinoKet's home page.
We don't want to make huge changes but creating a more professional and eye-catching style.

We need to look very serious like a professional services company and in the same time to look like a social network for e-commerce.

Our logo is very captive and you can use to creating something of harmonious.

This is a re-style and I'm excepted to see unique and fresh design like Glimmora.

Target Market(s)

e-commerce and social

Industry/Entity Type

Social

Number of Pages Required

1 page

Font styles to use
Serif
Sans Serif

Requirements
Must have
• An eye-catching result.
• Search bar with logo and Login How it works and business
• The slogan with login and signup.
• Footer links.
Nice to have
• I would like to open the home page and see only two clear ways:
• -Consumer
• --Search
• --The slogan
• --Login and Signup
• --How it works
• -Business
• --Go to Business area
• Background: City, Shopping.
Should not have
• Scrollbar style!

```html
<!DOCTYPE html>
<html lang="en">
<head>
<meta charset="utf-8">
<title>BrinoKet — Shop directly from your profile</title>
<link rel="stylesheet" href="https://fonts.googleapis.com/css2?family=Montserrat:wght@400;500;600;700&family=Open+Sans:wght@300;400&display=swap">
<style>
  :root {
    --night: #1c1d45;
    --header: rgba(22, 22, 56, 0.82);
    --white: #ffffff;
    --field-text: #3a3a3a;
    --placeholder: #8c8c8c;
    --chevron: #b5b5b5;
    --signup: #d0303a;
    --business: #7ab735;
    --muted: #e8e6f2;
  }
  * { box-sizing: border-box; margin: 0; padding: 0; }
  html, body { width: 1200px; height: 675px; overflow: hidden; }
  body { font-family: "Montserrat", sans-serif; color: var(--white); background: var(--night); }

  .home { position: relative; width: 1200px; height: 675px; overflow: hidden; }

  .city-backdrop {
    position: absolute; inset: 0;
    background:
      radial-gradient(ellipse at 22% 35%, rgba(150, 110, 120, 0.55), transparent 45%),
      radial-gradient(ellipse at 80% 30%, rgba(170, 120, 130, 0.45), transparent 45%),
      radial-gradient(ellipse at 50% 75%, rgba(90, 80, 130, 0.6), transparent 55%),
      linear-gradient(180deg, #4c4468 0%, #5a4f70 40%, #3b3660 70%, #272750 100%);
  }

  .site-header {
    position: absolute; top: 0; left: 0; width: 100%; height: 59px;
    background: var(--header);
  }
  .brand {
    position: absolute; left: 27px; top: 14px;
    font-size: 28px; font-weight: 700; letter-spacing: -0.5px; line-height: 30px;
    color: var(--white);
  }
  .feed-label {
    position: absolute; left: 292px; top: 22px;
    font-size: 11px; font-weight: 600;
  }
  .select {
    position: absolute; top: 13px; height: 33px;
    background: var(--white); border-radius: 3px;
    font-size: 12px; color: var(--field-text);
    display: flex; align-items: center; padding: 0 12px;
  }
  .select svg.chevron { position: absolute; right: 10px; top: 12px; }
  .select-interest { left: 396px; width: 175px; }
  .select-city { left: 581px; width: 176px; padding-left: 28px; }
  .select-city svg.pin { position: absolute; left: 11px; top: 9px; }
  .btn-signup {
    position: absolute; left: 770px; top: 13px; width: 83px; height: 33px;
    background: var(--signup); border-radius: 3px;
    font-size: 13px; font-weight: 500;
    display: flex; align-items: center; justify-content: center;
  }
  .link-login {
    position: absolute; left: 869px; top: 22px;
    font-size: 13px; font-weight: 500;
  }

  .app-preview {
    position: absolute; left: 505px; top: 100px; width: 190px; height: 219px;
    border-radius: 10px;
    background: radial-gradient(ellipse at 50% 55%, rgba(40, 42, 48, 0.85) 0 34%, rgba(255, 255, 255, 0.08) 35%, transparent 70%);
  }

  .slogan {
    position: absolute; left: 0; top: 336px; width: 1200px; text-align: center;
    font-family: "Open Sans", sans-serif; font-weight: 300; font-size: 33px;
  }

  .search {
    position: absolute; left: 399px; top: 391px; width: 400px; height: 36px;
    background: var(--white); border-radius: 3px;
    font-family: "Open Sans", sans-serif; font-size: 12.5px; color: var(--placeholder);
    display: flex; align-items: center; padding-left: 29px;
  }
  .search-icon { position: absolute; left: 816px; top: 400px; }

  .btn-business {
    position: absolute; left: 510px; top: 459px; width: 179px; height: 34px;
    background: var(--business); border-radius: 2px;
    font-size: 12.5px; font-weight: 500;
    display: flex; align-items: center; justify-content: center; gap: 6px;
  }
  .link-how {
    position: absolute; left: 0; top: 505px; width: 1200px; text-align: center;
    font-size: 11.5px; font-weight: 500;
  }

  .footer-nav {
    position: absolute; left: 0; top: 575px; width: 1200px;
    display: flex; justify-content: center; gap: 0;
    font-size: 10.5px; font-weight: 500; color: var(--muted);
  }
  .footer-nav span { padding: 0 13px; }
  .copyright {
    position: absolute; left: 0; top: 603px; width: 1200px; text-align: center;
    font-size: 9px; font-weight: 500; color: var(--muted);
  }
</style>
</head>
<body>
<main class="home">
  <div class="city-backdrop" role="img" aria-label="Blurred photo of a busy city shopping street with crowds of pedestrians"></div>

  <header class="site-header">
    <div class="brand">BrinoKet</div>
    <div class="feed-label">Setup your feed</div>
    <div class="select select-interest">Active life
      <svg class="chevron" width="13" height="8" viewBox="0 0 13 8"><path d="M1 1l5.5 5.5L12 1" fill="none" stroke="var(--chevron)" stroke-width="1.4"/></svg>
    </div>
    <div class="select select-city">
      <svg class="pin" width="10" height="14" viewBox="0 0 10 14"><path d="M5 0a5 5 0 0 0-5 5c0 3.6 5 9 5 9s5-5.4 5-9a5 5 0 0 0-5-5zm0 7a2 2 0 1 1 0-4 2 2 0 0 1 0 4z" fill="var(--chevron)"/></svg>
      London
      <svg class="chevron" width="13" height="8" viewBox="0 0 13 8"><path d="M1 1l5.5 5.5L12 1" fill="none" stroke="var(--chevron)" stroke-width="1.4"/></svg>
    </div>
    <div class="btn-signup">Sign Up</div>
    <div class="link-login">Login</div>
  </header>

  <div class="app-preview" role="img" aria-label="Illustration of a smartphone showing the shopping feed, surrounded by user avatars"></div>

  <h1 class="slogan">Shop directly from your profile</h1>

  <div class="search">Search keyword</div>
  <svg class="search-icon" width="19" height="19" viewBox="0 0 19 19"><circle cx="7.5" cy="7.5" r="5.8" fill="none" stroke="var(--white)" stroke-width="2.6"/><path d="M11.8 11.8l5.5 5.5" stroke="var(--white)" stroke-width="3" stroke-linecap="round"/></svg>

  <div class="btn-business">Go to Business Area
    <svg width="18" height="8" viewBox="0 0 18 8"><path d="M0 4h16M13 1l3.5 3L13 7" fill="none" stroke="var(--white)" stroke-width="1"/></svg>
  </div>
  <div class="link-how">How it works</div>

  <nav class="footer-nav">
    <span>About Us</span><span>Blog</span><span>Business</span><span>Jobs</span><span>Privacy</span><span>FAQ</span><span>Contacts</span>
  </nav>
  <div class="copyright">© 2015 BrinoKet. All right reserved.</div>
</main>
</body>
</html>
```